Upstart Retirement Planning Firm needs help with business card design

Harborview Nest Advisors, LLC is looking for help with business card design. We give advice on investments, insurance, and other financial matters related to retirement. There are some required disclosures that we will provide but mostly we are looking for a professional, classy business card that reflects the theme we have chosen. We have a logo that is attached but we would like to add a phrase; "Turning Your Earned Income Into Retirement Income"

Doubled sided only so that we can add the required disclosures (needed for our industry) on the back of the card. We will provide the exact words for this in 1-2 days.

Target Market(s)

Retirees and Pre-retirees. Professionals 50+ years old

Industry/Entity Type

Financial Planning

Contact Information for Business Card

We currently have two people who will need separate cards so we'd like to have a template so that we can add names for new cards in the future.

For the first run, please show the following information.

Gregor Pelham, MBA, ChFC®, CLU®
Financial Advisor, Registered Representative
gpelham@harborviewnest.example
Phone: (555) 318-2946
Toll Free Fax: (800) 555-0193

Address is
2187 Meadowlark Ridge Rd.
Suite K418
Virginia Beach, VA 23999

Colors
3277b5

Requirements
Must have
• Logo, contact info, small phase to describe business (in description), required legal disclosures on back of the card as follows (in small font)
• Gregor Pelham is a registered representative of and offers securities through Brightmoor Capital Brokerage Corporation, Member FNQX. Brightmoor Capital Brokerage Corporation is a member of the Brightmoor Capital Alliance which is the marketing name for Brightmoor Holding Corporation and its affiliates.
Nice to have
• Rounded edges, raised letters
Should not have
• any colors that aren't in the logo (other than black for font)

```html
<!DOCTYPE html>
<html lang="en">
<head>
<meta charset="utf-8">
<title>Harborview Nest Advisors – Business Card</title>
<link rel="stylesheet" href="https://fonts.googleapis.com/css2?family=Tinos:ital,wght@0,400;0,700;1,400&display=swap">
<style>
  :root {
    --brand-blue: #3277b5;
    --brand-blue-dark: #2a66a0;
    --brand-blue-light: #4a8cc8;
    --logo-grey: #9a9a9a;
    --ink: #1a1a1a;
    --paper: #ffffff;
    --paper-shade: #eef0f2;
    --backdrop: #e6e8eb;
  }
  * { box-sizing: border-box; margin: 0; padding: 0; }
  html, body { width: 1200px; height: 892px; overflow: hidden; }
  body {
    background: var(--backdrop);
    font-family: "Tinos", "Times New Roman", serif;
    color: var(--ink);
    display: flex;
    align-items: center;
    justify-content: center;
    gap: 40px;
  }
  .card {
    width: 540px;
    height: 309px;
    border-radius: 12px;
    position: relative;
    overflow: hidden;
    box-shadow: 0 6px 18px rgba(0,0,0,0.18);
  }

  /* Front */
  .card--front {
    background: linear-gradient(160deg, var(--paper) 55%, var(--paper-shade));
  }
  .advisor {
    position: absolute;
    left: 262px;
    top: 30px;
  }
  .advisor__name {
    font-weight: 700;
    font-size: 30px;
    line-height: 1.1;
    color: var(--brand-blue);
    letter-spacing: 0.3px;
  }
  .advisor__credentials,
  .advisor__title {
    font-size: 14px;
    line-height: 1.35;
  }
  .divider {
    position: absolute;
    left: 150px;
    right: 30px;
    top: 114px;
    height: 1.5px;
    background: var(--brand-blue);
  }
  .contact {
    position: absolute;
    left: 262px;
    top: 132px;
    list-style: none;
  }
  .contact__item {
    display: flex;
    align-items: flex-start;
    gap: 10px;
    font-size: 13.5px;
    line-height: 1.25;
    margin-bottom: 9px;
  }
  .contact__icon {
    width: 14px;
    height: 14px;
    flex: none;
    margin-top: 1px;
  }
  .firm-mark {
    position: absolute;
    left: 26px;
    top: 190px;
    width: 215px;
    display: flex;
    flex-direction: column;
    align-items: flex-start;
    gap: 7px;
  }
  .firm-mark__row {
    display: flex;
    align-items: center;
    gap: 10px;
  }
  .firm-mark__dot {
    width: 14px;
    height: 14px;
    border-radius: 50%;
    background: var(--brand-blue);
    flex: none;
  }
  .firm-mark__name {
    font-size: 21px;
    line-height: 1.1;
    color: var(--brand-blue);
  }
  .firm-mark__rule {
    width: 205px;
    height: 1px;
    background: var(--logo-grey);
  }
  .firm-mark__suffix {
    font-size: 11px;
    letter-spacing: 4px;
    color: var(--brand-blue);
    margin-left: 24px;
  }

  /* Back */
  .card--back {
    background: linear-gradient(200deg, var(--brand-blue-light), var(--brand-blue) 45%, var(--brand-blue-dark));
    color: var(--paper);
    display: flex;
    flex-direction: column;
    align-items: center;
    padding: 26px 30px 18px;
  }
  .back-mark__name {
    font-size: 38px;
    line-height: 1.05;
    text-align: center;
  }
  .back-mark__rule {
    width: 280px;
    height: 1.5px;
    background: var(--paper);
    margin-top: 12px;
  }
  .back-mark__suffix {
    font-size: 16px;
    letter-spacing: 5px;
    margin-top: 8px;
  }
  .tagline {
    font-style: italic;
    font-size: 14px;
    margin-top: 12px;
    text-align: center;
  }
  .disclosure {
    margin-top: auto;
    font-size: 9px;
    line-height: 1.35;
    text-align: center;
    opacity: 0.92;
  }
</style>
</head>
<body>
  <section class="card card--front" aria-label="Business card front">
    <div class="advisor">
      <h1 class="advisor__name">Gregor Pelham</h1>
      <p class="advisor__credentials">MBA, ChFC®, CLU®</p>
      <p class="advisor__title">Financial Advisor, Registered Representative</p>
    </div>
    <div class="divider"></div>
    <ul class="contact">
      <li class="contact__item">
        <svg class="contact__icon" viewBox="0 0 14 14" aria-hidden="true">
          <rect width="14" height="14" fill="#1a1a1a"/>
          <path d="M4 3.2 L5.6 3 L6.3 5 L5.3 5.8 Q6.2 7.8 8.2 8.7 L9 7.7 L11 8.4 L10.8 10 Q6 10.3 4 3.2 Z" fill="#fff"/>
        </svg>
        <span>(555) 318-2946</span>
      </li>
      <li class="contact__item">
        <svg class="contact__icon" viewBox="0 0 14 14" aria-hidden="true">
          <rect width="14" height="14" fill="#1a1a1a"/>
          <rect x="4.5" y="2.5" width="5" height="3" fill="#fff"/>
          <rect x="3" y="6" width="8" height="4.5" fill="#fff"/>
          <rect x="4.5" y="9" width="5" height="2.5" fill="#fff"/>
        </svg>
        <span>(800) 555-0193</span>
      </li>
      <li class="contact__item">
        <svg class="contact__icon" viewBox="0 0 14 14" aria-hidden="true">
          <rect width="14" height="14" fill="#1a1a1a"/>
          <rect x="3" y="4" width="8" height="6" fill="#fff"/>
          <path d="M3 4 L7 7.3 L11 4" fill="none" stroke="#1a1a1a" stroke-width="0.9"/>
        </svg>
        <span>gpelham@harborviewnest.example</span>
      </li>
      <li class="contact__item">
        <svg class="contact__icon" viewBox="0 0 14 14" aria-hidden="true">
          <rect width="14" height="14" fill="#1a1a1a"/>
          <path d="M7 2.5 A3 3 0 0 1 10 5.5 Q10 7.5 7 11.5 Q4 7.5 4 5.5 A3 3 0 0 1 7 2.5 Z" fill="#fff"/>
          <circle cx="7" cy="5.5" r="1.1" fill="#1a1a1a"/>
        </svg>
        <span>2187 Meadowlark Ridge Rd., Suite K418<br>Virginia Beach, VA 23999</span>
      </li>
    </ul>
    <div class="firm-mark">
      <div class="firm-mark__row">
        <span class="firm-mark__dot"></span>
        <span class="firm-mark__name">Harborview Nest Advisors</span>
      </div>
      <div class="firm-mark__rule"></div>
      <span class="firm-mark__suffix">LLC</span>
    </div>
  </section>

  <section class="card card--back" aria-label="Business card back">
    <p class="back-mark__name">Harborview Nest Advisors</p>
    <div class="back-mark__rule"></div>
    <p class="back-mark__suffix">LLC</p>
    <p class="tagline">Turning Your Earned Income Into Retirement Income</p>
    <p class="disclosure">Gregor Pelham is a registered representative of and offers securities through Brightmoor Capital Brokerage Corporation, Member FNQX. Brightmoor Capital Brokerage Corporation is a member of the Brightmoor Capital Alliance which is the marketing name for Brightmoor Holding Corporation and its affiliates.</p>
  </section>
</body>
</html>
```